Maple n Brook - Contact/Landing Page

I need a landing page which will essentially be the page that customers will go to from the 'website' link on QTV listing. It will provide a short overview of services which need to be selectable. a little further down can capture some contact details followed by a large Submit Now button etc...

I have some icon/logo's that can be utilised at the bottom of the page as industry type references.

Target Market(s)

End of Lease Cleaning Services

Industry/Entity Type

Cleaning Service

Colors

Designer to choose colors to be used in the design.

Requirements
Must have
• As per description
Should not have
• Colours to match my website maplenbrook.com.au

```html
<!DOCTYPE html>
<html lang="en">
<head>
<meta charset="utf-8">
<title>Maple n Brook – End Of Lease Cleaning</title>
<link href="https://fonts.googleapis.com/css2?family=Tinos&family=Lato:wght@400;700&display=swap" rel="stylesheet">
<style>
:root{
  --brand:#1277c2;
  --brand-soft:#7fb2dc;
  --ink:#1b1b1b;
  --text:#2b2b2b;
  --line:#b9b9b9;
  --white:#ffffff;
  --footer:#000000;
  --mist:#e9eef4;
}
*{box-sizing:border-box;margin:0;padding:0}
html,body{width:1200px;height:2799px;overflow:hidden;background:var(--white)}
body{position:relative;font-family:'Lato',sans-serif;color:var(--text)}
.abs{position:absolute}
.serif{font-family:'Tinos',serif}

/* header */
.hero{left:0;top:0;width:1200px;height:625px;background:var(--brand)}
.menu-toggle{left:86px;top:30px;width:30px;height:28px}
.menu-toggle span{display:block;height:2px;background:var(--white);margin-bottom:11px}
.brand-mark{left:0;top:170px;width:1200px;text-align:center}
.brand-mark .square{display:inline-block;width:90px;height:90px;background:#b7c3cf;margin-bottom:26px}
.brand-mark .name{font-family:'Lato',sans-serif;font-weight:700;font-size:58px;color:#a9c8e6;letter-spacing:1px}
.tagline{left:0;top:490px;width:1200px;text-align:center;color:var(--white);font-size:41px}

/* section heading */
.section-title{left:0;width:1200px;text-align:center;font-size:43px;color:var(--ink)}
.rule{height:2px;background:var(--brand);width:106px}

/* services */
.card{top:837px;width:322px;height:386px;background:var(--white);box-shadow:0 2px 8px rgba(0,0,0,.22);text-align:center}
.card .photo{height:192px;width:100%}
.card h3{font-family:'Tinos',serif;font-weight:400;color:var(--brand);font-size:18px;margin-top:30px;letter-spacing:.3px}
.card p{font-size:15px;line-height:22px;margin:18px auto 0;width:270px;color:#222}
.select-btn{display:inline-flex;align-items:center;gap:10px;margin-top:18px;height:37px;padding:0 14px;background:var(--brand);color:var(--white);font-family:'Tinos',serif;font-size:14px;box-shadow:0 2px 4px rgba(0,0,0,.25)}

/* contact */
.contact-band{left:0;top:1309px;width:1200px;height:689px;background:linear-gradient(90deg,#e4e9ef,#f3f5f8 50%,#e1e7ee)}
.form-panel{left:154px;top:1357px;width:444px;height:592px;background:var(--white)}
.form-panel h2{position:absolute;top:38px;width:100%;text-align:center;font-weight:400;font-size:42px;color:var(--ink)}
.field{position:absolute;left:38px;width:372px;height:53px;border:1px solid var(--line);font-size:15px;padding-left:15px;line-height:51px;color:#222}
.submit-btn{position:absolute;left:169px;top:515px;width:108px;height:34px;background:var(--brand);color:var(--white);font-family:'Tinos',serif;font-size:17px;text-align:center;line-height:34px}
.info-panel{left:598px;top:1357px;width:448px;height:592px;background:linear-gradient(160deg,#3a8fd0,#2b83c9 60%,#3d8ccb)}
.info-item{left:681px;display:flex;align-items:center;gap:18px;color:var(--white);font-weight:700;font-size:21px}
.info-item .icon{width:53px;height:53px;border-radius:50%;background:var(--white);display:flex;align-items:center;justify-content:center;flex:none}

/* clients */
.client{top:2205px;width:218px;height:84px;border:1px solid #8c8c8c;display:flex;align-items:center;justify-content:center;gap:10px;font-family:'Lato',sans-serif;font-weight:700;font-size:21px;color:#1d3f8a}
.client .dot{width:26px;height:26px;background:#1d3f8a}
.badge-shape{width:216px;height:82px;background:#111}
.arrow{top:2232px;width:20px;height:28px}

/* footer */
.footer{left:0;top:2376px;width:1200px;height:423px;background:var(--footer);color:var(--white)}
.footer-brand{position:absolute;top:60px;width:100%;text-align:center;font-weight:700;font-size:26px;color:#5d9bd6}
.footer-nav{position:absolute;top:176px;width:100%;text-align:center;font-family:'Tinos',serif;font-size:16px}
.footer-nav span{margin:0 13px}
.footer-links{position:absolute;top:230px;width:100%;text-align:center;font-size:12px}
.socials{position:absolute;top:276px;left:520px;display:flex;gap:10px}
.socials span{width:33px;height:33px;border-radius:50%}
.socials .fill{background:var(--brand)}
.socials .ring{border:1.5px solid var(--white)}
.footer-rule{position:absolute;left:86px;top:347px;width:1028px;height:1px;background:#8a8a8a}
.licence{position:absolute;left:86px;top:376px;font-size:15px}
.copyright{position:absolute;left:0;top:376px;width:1200px;text-align:center;font-size:15px}
</style>
</head>
<body>

<header class="abs hero">
  <div class="abs menu-toggle"><span></span><span></span><span></span></div>
  <div class="abs brand-mark">
    <div class="square"></div>
    <div class="name">Maple n Brook</div>
  </div>
  <div class="abs tagline serif">End Of Lease Cleaning | Licensed Pest Control</div>
</header>

<div class="abs section-title serif" style="top:700px">OUR SERVICES</div>
<div class="abs rule" style="left:547px;top:767px"></div>

<article class="abs card" style="left:86px">
  <div class="photo" role="img" aria-label="Cleaners vacuuming and wiping an office" style="background:linear-gradient(135deg,#d9dde2,#8a8f96 60%,#3d4a5a)"></div>
  <h3>CLEANING</h3>
  <p>All Interior cleaning Carried ouy to Property Management Requirements.</p>
  <div class="select-btn">SELECT
    <svg width="16" height="16" viewBox="0 0 16 16" fill="none" stroke="#fff" stroke-width="2"><rect x="1" y="3" width="12" height="12" rx="2"/><path d="M4 8l3 3 8-9"/></svg></div>
</article>
<article class="abs card" style="left:438px">
  <div class="photo" role="img" aria-label="Cleaner vacuuming a living room carpet" style="background:linear-gradient(135deg,#e4e2de,#b9a692 55%,#3f7fb0)"></div>
  <h3>CARPET CLEANING</h3>
  <p>Carpet Steam Cleaning to Australian Standard As 3733:1995</p>
  <div class="select-btn">SELECT
    <svg width="16" height="16" viewBox="0 0 16 16" fill="none" stroke="#fff" stroke-width="2"><rect x="1" y="3" width="12" height="12" rx="2"/><path d="M4 8l3 3 8-9"/></svg></div>
</article>
<article class="abs card" style="left:790px">
  <div class="photo" role="img" aria-label="Technician spraying pest treatment in a cabinet" style="background:linear-gradient(135deg,#b0714a,#7c4f34 55%,#2e3442)"></div>
  <h3>PEST CONTROL</h3>
  <p>Pest Control Mandatory Reqirement for pest on premises.</p>
  <div class="select-btn">SELECT
    <svg width="16" height="16" viewBox="0 0 16 16" fill="none" stroke="#fff" stroke-width="2"><rect x="1" y="3" width="12" height="12" rx="2"/><path d="M4 8l3 3 8-9"/></svg></div>
</article>

<section class="abs contact-band" role="img" aria-label="Bright room with a cleaner mopping the floor"></section>

<form class="abs form-panel">
  <h2 class="serif">GET IN TOUCH</h2>
  <div class="abs rule" style="left:170px;top:100px"></div>
  <div class="field" style="top:131px">First Name:</div>
  <div class="field" style="top:207px">Sure Name:</div>
  <div class="field" style="top:282px">Email:</div>
  <div class="field" style="top:357px">Phone:</div>
  <div class="field" style="top:432px">Suburb:</div>
  <div class="submit-btn">SUBMIT</div>
</form>

<div class="abs info-panel" role="img" aria-label="Blue-tinted view of a cleaner mopping"></div>
<div class="abs info-item" style="top:1532px">
  <span class="icon"><svg width="26" height="26" viewBox="0 0 24 24" fill="#1277c2"><path d="M6.6 2.5l2.6 3.6-1.7 2.2c1 2.3 2.6 4 4.9 5.3l2.1-1.6 3.7 2.5-1.3 3.3c-6.7-.3-12.2-6.5-12-13z"/><path d="M15 5a4 4 0 0 1 3 3M15 2a7 7 0 0 1 6 6" stroke="#1277c2" stroke-width="1.6" fill="none"/></svg></span>
  <span>(123) 456 789</span>
</div>
<div class="abs info-item" style="top:1626px">
  <span class="icon"><svg width="28" height="22" viewBox="0 0 28 22" fill="none" stroke="#1277c2" stroke-width="2.2"><rect x="2" y="2" width="24" height="18" rx="3"/><path d="M3 4l11 9 11-9"/></svg></span>
  <span>info@maplenbrook.com.au</span>
</div>
<div class="abs info-item" style="top:1719px">
  <span class="icon"><svg width="20" height="26" viewBox="0 0 20 26" fill="#1277c2"><path d="M10 1a8 8 0 0 0-8 8c0 6 8 16 8 16s8-10 8-16a8 8 0 0 0-8-8zm0 11a3 3 0 1 1 0-6 3 3 0 0 1 0 6z"/></svg></span>
  <span style="line-height:27px">123,Lorem ipsum dolor<br>&nbsp;consectetur adipiscing.</span>
</div>

<div class="abs section-title serif" style="top:2074px">OUR CLIENT</div>
<div class="abs rule" style="left:547px;top:2141px"></div>

<svg class="abs arrow" style="left:40px" viewBox="0 0 20 28"><path d="M14 4L5 14l9 10" stroke="#111" stroke-width="2.5" fill="none"/></svg>
<div class="abs client" style="left:135px"><span class="dot"></span>Vertex Systems</div>
<div class="abs client" style="left:372px;border-color:#8c8c8c"><div class="badge-shape"></div></div>
<div class="abs client" style="left:609px;background:#8bbf3f;color:#ffffff;border-color:#111;border-bottom:6px solid #111">Harbour College</div>
<div class="abs client" style="left:847px">Lumen Training</div>
<svg class="abs arrow" style="left:1144px" viewBox="0 0 20 28"><path d="M6 4l9 10-9 10" stroke="#111" stroke-width="2.5" fill="none"/></svg>

<footer class="abs footer">
  <div class="footer-brand">Maple n Brook</div>
  <nav class="footer-nav"><span>Home</span><span>About Us</span><span>Services</span><span>Contact Us</span></nav>
  <div class="footer-links">FAQ &nbsp;| Tearm &nbsp;| privacy &amp; Policy &nbsp;| Services</div>
  <div class="socials"><span class="fill"></span><span class="ring"></span><span class="fill"></span><span class="ring"></span></div>
  <div class="footer-rule"></div>
  <div class="licence">Pest Licence: 4817362</div>
  <div class="copyright">© Copyright 2021 maplenbrook.All right Reserved.</div>
</footer>

</body>
</html>
```